Brintel Works - Fast, Efficient and Gas Mainteance for Domestic, Commercial and Industrial clients

We are in the process of purchasing a new business and would like to get a new logo and business card.
Business is a gas maintenance business that also does new gas installations.
Has been established since 1988.
Services include:
Install all types of gas appliances & equipment inc. hot water units
Maintain / repair / replace all types of gas appliances & equipment

Target Market(s)

Domestic, Commercial and Industrial clients

Industry/Entity Type

Business

Contact Information for Business Card

admin@brintelworks.com.au
07 3918 4726
Brintel Works PTY LTD

Logo Text

Gas Fitting & Plumbing Maintenance Specialists

Font styles to use
Sans Serif

Requirements
Must have
• Logo
• Business name, contact number, email address, web address
• Domestic | Commercial | Industrial Est Since 1988
Nice to have
• Possibly a black card with a flame logo to one side
Should not have
• Spelling errors

```html
<!DOCTYPE html>
<html lang="en">
<head>
<meta charset="utf-8">
<title>Brintel Works – Business Card</title>
<link rel="stylesheet" href="https://fonts.googleapis.com/css2?family=Open+Sans:wght@400;600&display=swap">
<style>
  :root {
    --backdrop: #2b2b2b;
    --card: #1c1c1c;
    --card-edge: #262626;
    --ink: #f2f2f2;
    --orange: #f39a1e;
    --yellow: #f5c518;
    --divider: #333333;
  }
  * { margin: 0; padding: 0; box-sizing: border-box; }
  html, body {
    width: 1200px; height: 900px; overflow: hidden;
    background: var(--backdrop);
    font-family: "Open Sans", sans-serif;
  }
  .stage {
    width: 1200px; height: 900px;
    display: flex; align-items: center; justify-content: center; gap: 60px;
  }
  .card {
    position: relative;
    width: 520px; height: 300px;
    background: var(--card);
    border: 1px solid var(--card-edge);
    border-radius: 22px;
    box-shadow: 0 14px 30px rgba(0,0,0,.45);
    overflow: hidden;
  }

  /* Contact side */
  .card-contact .brand-block {
    position: absolute; left: 30px; top: 70px; width: 190px; height: 130px;
    display: flex; flex-direction: column; align-items: center; justify-content: center; gap: 14px;
  }
  .brand-dot {
    width: 46px; height: 46px; border-radius: 50%;
    background: var(--orange);
  }
  .brand-name {
    color: var(--orange); font-weight: 600; font-size: 22px; letter-spacing: .5px;
  }
  .divider {
    position: absolute; left: 240px; top: 40px; width: 1px; height: 170px;
    background: var(--divider);
  }
  .contact {
    position: absolute; left: 262px; top: 46px;
    color: var(--ink); font-size: 14px; line-height: 1.5;
  }
  .contact .address { margin-bottom: 18px; }
  .contact ul { list-style: none; }
  .contact li { display: flex; align-items: center; gap: 10px; }
  .contact svg { width: 12px; height: 12px; flex: none; }
  .tagline {
    position: absolute; left: 0; right: 0; bottom: 34px;
    text-align: center; color: var(--orange); font-weight: 600; font-size: 15.5px;
  }

  /* Logo side */
  .card-logo {
    display: flex; flex-direction: column; align-items: center; justify-content: center; gap: 16px;
  }
  .card-logo .brand-dot { width: 54px; height: 54px; }
  .card-logo .brand-name { color: var(--yellow); font-size: 34px; }
</style>
</head>
<body>
<main class="stage">
  <section class="card card-contact" aria-label="Card back with contact details">
    <div class="brand-block">
      <span class="brand-dot" aria-hidden="true"></span>
      <span class="brand-name">Brintel Works</span>
    </div>
    <div class="divider"></div>
    <div class="contact">
      <p class="address">12345, Address Goes Here<br>Country Name, 123456</p>
      <ul>
        <li>
          <svg viewBox="0 0 12 12" aria-hidden="true"><path fill="var(--orange)" d="M2.4 0.8l2 1.9-1 1.3c.7 1.5 1.8 2.6 3.3 3.3l1.3-1 1.9 2-1.2 1.6C5 9.5 2.5 7 1 3.2z"/></svg>
          <span>07 3918 4726</span>
        </li>
        <li>
          <svg viewBox="0 0 12 12" aria-hidden="true"><rect x="0.5" y="2" width="11" height="8" rx="1" fill="var(--orange)"/><path d="M1 2.6l5 3.8 5-3.8" stroke="var(--card)" stroke-width="1" fill="none"/></svg>
          <span>admin@brintelworks.com.au</span>
        </li>
        <li>
          <svg viewBox="0 0 12 12" aria-hidden="true"><g fill="none" stroke="var(--orange)" stroke-width="1.6" stroke-linecap="round"><path d="M5 7l2-2"/><path d="M4.3 5.3L2.6 7a1.8 1.8 0 0 0 2.5 2.5l1.6-1.7"/><path d="M7.7 6.7L9.4 5a1.8 1.8 0 0 0-2.5-2.5L5.3 4.2"/></g></svg>
          <span>www.brintelworks.com.au</span>
        </li>
      </ul>
    </div>
    <p class="tagline">Domestic | Commercial | Industrial Est Since 1988</p>
  </section>

  <section class="card card-logo" aria-label="Card front with business name">
    <span class="brand-dot" aria-hidden="true"></span>
    <span class="brand-name">Brintel Works</span>
  </section>
</main>
</body>
</html>
```